New Joomla Website for Marquee Hire Co

We need a web design for our new Marquee Hire Co here in New Zealand called Breezy Canopies.
We rather like the retro look, as it fit very well with the current trends in weddings that is a more of a retro look (and we had our logo designed to reflect that!). The 50's and 60's wedding styles are really making a comeback. We would like to communicate to that market effectively.

The Home page should have a slider image with space for a headline on it. It is a visual product we have (but we are selling that dream of a perfect wedding/party/event).

Our competition here have a really nice site that you could look at - www.plovanto.co.nz

The other pages would have space for a picture, and then a blurb under each element related to it.
We will have a FAQ, Gallery, Hire and Contact us pages - we will add them as we go along.

From a technical perspective, we are using Joomla 2.5 and upwards.

Any questions - let me know. I look forward seeing the designs!

Target Market(s)

Couples looking for a wedding marquee, birthday parties, Corporate events

Industry/Entity Type

Wedding

Requirements
Must have
• 1. Preferably done in Joomla. I will also look at Wordpress site.
2. It has to have a retro look and feel.
3. It has to use my brand new logo (included)

```html
<!DOCTYPE html>
<html lang="en">
<head>
<meta charset="utf-8">
<title>Breezy Canopies – Marquee Hire New Zealand</title>
<link href="https://fonts.googleapis.com/css2?family=Arimo:wght@400;700&family=Italianno&family=Londrina+Outline&display=swap" rel="stylesheet">
<style>
:root{
  --page:#eef0f0;
  --panel:#ffffff;
  --frame:#e6e9e9;
  --nav:#3c78b5;
  --brown:#5a4330;
  --brown-dark:#3f2d1f;
  --text:#666666;
  --cyan:#33c6f4;
  --link:#1a86c8;
  --footer-top:#4a4a4a;
  --footer-bottom:#2b2b2b;
  --dot:#6a6a6a;
  --dot-active:#6b8fae;
}
*{box-sizing:border-box;margin:0;padding:0}
html,body{width:1141px;height:1200px;overflow:hidden;background:var(--page)}
body{font-family:"Arimo",Arial,sans-serif;color:var(--text)}
.stage{position:relative;width:1150px;height:1209px;transform:scale(.9922);transform-origin:0 0}
.abs{position:absolute}

.contact-top{left:96px;top:30px;display:flex;gap:14px;align-items:center;font-size:16px;color:#4a3d33;line-height:26px}
.search{left:762px;top:38px;width:292px;height:33px;background:#fff;border:1px solid #d6d6d6;font-size:11px;color:#888;padding:10px 13px}
.search svg{position:absolute;right:12px;top:8px}

.main-panel{left:87px;top:99px;width:977px;height:945px;background:var(--panel);border:1px solid #dfe2e2;border-radius:3px}

.nav a{position:absolute;top:124px;font-family:"Londrina Outline",sans-serif;font-size:30px;color:var(--nav);text-decoration:underline;text-underline-offset:3px;text-transform:uppercase}

.brand{left:440px;top:80px;width:270px;height:40px;display:flex;align-items:center;justify-content:center;gap:10px}
.brand-dot{width:16px;height:16px;border-radius:50%;background:var(--brown)}
.brand-name{color:var(--brown);font-family:"Arimo",sans-serif;font-weight:700;font-size:24px;white-space:nowrap}

.slider-frame{left:95px;top:199px;width:960px;height:390px;background:var(--frame);border-radius:3px}
.slider-img{left:104px;top:208px;width:942px;height:370px;background:linear-gradient(180deg,#3f5a2c 0%,#6e8a52 22%,#e9ecef 40%,#d8dbdf 60%,#8c6f5e 80%,#5b7a3e 100%)}
.slider-shadow{left:110px;top:588px;width:930px;height:24px;background:radial-gradient(ellipse at top,rgba(0,0,0,.22),transparent 70%)}
.caption{left:725px;top:300px;width:291px;height:187px;background:rgba(255,255,255,.94);border-radius:3px;text-align:center;padding-top:17px}
.caption h2{font-size:21px;line-height:28px;color:var(--brown);font-weight:700}
.caption hr{border:0;border-top:1px solid #e2e2e2;margin:17px 18px 20px}
.dots{display:flex;justify-content:center;gap:15px}
.dots span{width:16px;height:16px;border-radius:50%;background:var(--dot)}
.dots span:first-child{background:var(--dot-active)}

.script{font-family:"Italianno",cursive;color:var(--brown);font-weight:400}
.welcome h1{position:absolute;left:97px;top:624px;font-size:42px}
.welcome p{position:absolute;left:97px;top:676px;width:616px;font-size:13px;line-height:22px;text-align:justify}
.divider{left:96px;top:823px;width:617px;border-top:1px solid #dcdcdc}

.pricing-bg{left:104px;top:887px;width:616px;height:153px;background:linear-gradient(180deg,#f4f5f4,#fbfbfb)}
.pricing-photo{left:125px;top:862px;width:206px;height:150px;background:#fff;box-shadow:0 1px 4px rgba(0,0,0,.3);padding:4px}
.pricing-photo div{width:100%;height:100%;background:linear-gradient(160deg,#3a2d4a,#8a7aa8 35%,#2a221c 70%,#6b5638)}
.pricing h3{position:absolute;left:372px;top:855px;font-size:31px}
.pricing p{position:absolute;left:371px;top:898px;width:320px;font-size:13px;line-height:22px}
.btn{left:370px;top:972px;width:176px;height:40px;border-radius:20px;background:linear-gradient(180deg,#7b5d42,var(--brown-dark));color:#fff;font-weight:700;font-size:16px;display:flex;align-items:center;padding-left:24px;gap:14px}
.btn i{width:20px;height:20px;border-radius:50%;background:#3a2a1c;display:flex;align-items:center;justify-content:center}

.side-box{background:var(--frame);border-radius:3px}
.gallery{left:747px;top:632px;width:292px;height:191px}
.gallery h4,.testimonials h4{position:absolute;left:78px;top:2px;font-size:30px}
.gallery-bloom{left:754px;top:634px;width:56px;height:48px;border-radius:50%;background:radial-gradient(circle,#f6b7cf,#f4d9e5 60%,transparent 70%)}
.gallery-photo{left:755px;top:670px;width:276px;height:145px;background:#fff;padding:4px}
.gallery-photo div{width:100%;height:100%;background:linear-gradient(135deg,#5d7f48,#c8cfd8 40%,#8aa2bf 65%,#e8e2d8)}

.testimonials{left:747px;top:843px;width:292px;height:191px}
.test-card{left:756px;top:880px;width:275px;height:146px;background:#fff;border-radius:3px;padding:22px 16px 0 12px;font-size:13px;line-height:22px;font-style:italic;text-align:justify}
.test-card .quote{font-family:Georgia,serif;font-size:20px;line-height:10px;color:#777;font-style:normal}
.test-card .client{font-style:normal;color:#4a3a2c;margin-top:2px}
.bubble{left:759px;top:851px;width:46px;height:38px;background:linear-gradient(#fff,#d9e7f2);border:1px solid #b9cfe0;border-radius:4px}

.social-bar{left:87px;top:1050px;width:977px;height:64px;background:var(--cyan);border-radius:3px}
.social-icon{left:104px;top:1062px;width:40px;height:40px;border-radius:50%;background:#fff}
.social-title{left:172px;top:1067px;color:#fff;font-weight:700;font-size:21px;font-family:"Arimo",sans-serif}
.social-msg{left:321px;top:1057px;width:734px;height:51px;background:#fff;border-radius:26px;padding:8px 90px 0 37px;font-size:13px;line-height:18px}
.social-msg a{color:var(--link);text-decoration:none}
.social-next{left:1022px;top:1072px;width:22px;height:22px;border-radius:50%;background:#e4e4e4;display:flex;align-items:center;justify-content:center}

.footer{left:87px;top:1120px;width:977px;height:85px;background:linear-gradient(180deg,var(--footer-top),var(--footer-bottom));border-radius:2px;color:#e8e8e8;font-size:13px}
.footer-links{position:absolute;left:9px;top:18px}
.footer-copy{position:absolute;left:9px;top:50px}
.share{position:absolute;top:31px;width:22px;height:22px;border-radius:3px}
</style>
</head>
<body>
<div class="stage">

  <div class="abs contact-top">
    <svg width="32" height="26" viewBox="0 0 32 26" aria-hidden="true"><path d="M2 9c0-5 28-5 28 0l-2 4-6-1v-3c-3-1-9-1-12 0v3l-6 1z" fill="#6b5443"/><rect x="7" y="12" width="18" height="12" rx="3" fill="#6b5443"/><circle cx="16" cy="18" r="3" fill="#eee"/></svg>
    <div>Call us : 555 408 7219<br>Email &nbsp;: info@breezycanopies.co.nz</div>
  </div>

  <div class="abs search">Search
    <svg width="16" height="16" viewBox="0 0 16 16" aria-hidden="true"><circle cx="6" cy="6" r="4.5" fill="none" stroke="#222" stroke-width="2.5"/><path d="M9.5 9.5 14 14" stroke="#222" stroke-width="3"/></svg>
  </div>

  <div class="abs main-panel"></div>

  <nav class="nav">
    <a style="left:116px">Home</a>
    <a style="left:229px">FAQ</a>
    <a style="left:325px">Gallery</a>
    <a style="left:737px">Hire</a>
    <a style="left:862px">Contact us</a>
  </nav>

  <div class="abs brand">
    <span class="brand-dot"></span>
    <span class="brand-name">Breezy Canopies</span>
  </div>

  <div class="abs slider-frame"></div>
  <div class="abs slider-img" role="img" aria-label="Guests mingling outside a large white stretch marquee on a garden lawn"></div>
  <div class="abs slider-shadow"></div>
  <div class="abs caption">
    <h2>Fusce erat augue,<br>rutrum vel pharetra a,<br>aliquet ac mauris</h2>
    <hr>
    <div class="dots"><span></span><span></span><span></span><span></span></div>
  </div>

  <section class="welcome">
    <h1 class="script">Welcome to our site</h1>
    <p>Donec vehicula nibh non quam pellentesque vitae cursus magna vestibulum. Quisque convallis, eros imperdiet lobortis consectetur, massa erat pretium risus, elementum suscipit nisi dolor sed dui. Curabitur est magna, porta id condimentum non, congue eu elit. Fusce dictum commodo odio, a laoreet lacus dictum non. Fusce iaculis egestas scelerisque. Mauris at dignissim risus. Nullam vitae lacus a lorem adipiscing ultricies. Lorem ipsum dolor sit amet, consectetur adipiscing elit. In pulvinar scelerisque felis at ultricies. Nam in sem ac quam feugiat egestas. Nunc volutpat justo at magna fringilla venenatis.</p>
  </section>
  <div class="abs divider"></div>

  <section class="pricing">
    <div class="abs pricing-bg"></div>
    <div class="abs pricing-photo"><div role="img" aria-label="Marquee interior set for an evening reception with draped lighting"></div></div>
    <h3 class="script">View our affordable Pricing list</h3>
    <p>Mauris at dignissim risus. Nullam vitae lacus a lorem adipiscing elit. In pulvinar scelerisque felis at ultricies. Nam in sem ac quam.</p>
    <div class="abs btn">SELECT NOW <i><svg width="8" height="10" viewBox="0 0 8 10"><path d="M2 1l4 4-4 4" fill="none" stroke="#fff" stroke-width="2"/></svg></i></div>
  </section>

  <aside>
    <div class="abs side-box gallery"><h4 class="script">Our Gallery</h4></div>
    <div class="abs gallery-bloom" role="img" aria-label="Pink lily flower"></div>
    <div class="abs gallery-photo"><div role="img" aria-label="Bridesmaids in blue dresses at a garden wedding"></div></div>

    <div class="abs side-box testimonials"><h4 class="script">Testimonials</h4>
      <svg class="abs" style="left:258px;top:12px" width="10" height="12" viewBox="0 0 10 12"><path d="M2 1l5 5-5 5" fill="none" stroke="#777" stroke-width="2"/></svg>
    </div>
    <div class="abs bubble"></div>
    <div class="abs test-card">
      <span class="quote">“</span> Maecenas vehicula dui at neque consectetur eu aliquet purus ultricies. Fusce erat augue, rutrum vel pharetra a, aliquet ac mauris metus eu lectus. <span class="quote">”</span>
      <div class="client">Client Name, City</div>
    </div>
  </aside>

  <div class="abs social-bar"></div>
  <div class="abs social-icon"></div>
  <div class="abs social-title">Social Feed</div>
  <div class="abs social-msg">Mauris at dignissim risus. <a>http://www.kelmora.net/news/72ab</a> adipiscing elit. In pulvinar scelerisque felis at ultricies. Nam in sem ac quam.</div>
  <div class="abs social-next"><svg width="8" height="10" viewBox="0 0 8 10"><path d="M2 1l4 4-4 4" fill="none" stroke="#fff" stroke-width="2"/></svg></div>

  <footer class="abs footer">
    <div class="footer-links">Home &nbsp; | &nbsp; FAQ &nbsp; | &nbsp; Gallery &nbsp; | &nbsp; Hire &nbsp; | &nbsp; Contact us</div>
    <div class="footer-copy">Copyright © &nbsp;2013 &nbsp;www.breezycanopies.co.nz &nbsp;&nbsp;All rights reserved.</div>
    <span class="share" style="left:914px;background:#3b5998"></span>
    <span class="share" style="left:944px;background:#3fb6e8"></span>
  </footer>

</div>
</body>
</html>
```